High-end construction company needs a business card design

We need a modern looking business card that draws people in, is memorable and looks so good people will want to sick it on their fridges.
On the first side what is needed are:
Logo
My name - Tomasz Brelwik
Title - Managing Director
Website - www.varkelt.co.uk
Email - tomasz@varkelt.co.uk
Telephone - 020 5194 6281
Mobile - 07845139072
On the back side was is needed is a list of all the services we provide:
-Kitchen Renovations
-Bathroom Renovations
-House Renovations
-Garage Conversions
-Extensions
-Loft Conversions
-Conservatories
-Carpentry
-Tiling
-Electrical
-Plumbing & Heating
-Bricklaying
-Landscaping
-Decorating
-Plastering
We would like the colours to be the same shades as on the logo with grey or black for the words.
Target Market(s)
Anyone who needs building work done
Contact Information for Business Card
This business card is for a construction company which strives to deliver excellent service and quality.
The look and feel of the card should represent this.
Requirements
Must have
- On the first side what is needed are:
Logo
My name - Tomasz Brelwik
Title - Managing Director
Website - www.varkelt.co.uk
Email - tomasz@varkelt.co.uk
Telephone - 020 5194 6281
Mobile - 07845139072
Nice to have
- Cool looking features

```html
<!DOCTYPE html>
<html lang="en">
<head>
<meta charset="utf-8">
<title>Varkelt Construction Ltd – Business Card</title>
<link rel="stylesheet" href="https://fonts.googleapis.com/css2?family=Russo+One&family=Arimo:wght@400;700&display=swap">
<style>
  :root{
    --bg:#2b2b2b;
    --green:#6cbf3f;
    --green-dark:#3f8a36;
    --green-light:#79c243;
    --ink:#333333;
    --paper:#ffffff;
    --rule:#d9d9d9;
  }
  *{box-sizing:border-box;margin:0;padding:0}
  html,body{width:1200px;height:866px;overflow:hidden;background:var(--bg)}
  .sheet{position:relative;width:1200px;height:866px}
  .card{position:absolute;left:280px;width:640px;height:366px;overflow:hidden;box-shadow:0 10px 24px rgba(0,0,0,.45)}
  .card--front{top:52px;background:var(--paper)}
  .card--back{top:448px;background:linear-gradient(135deg,var(--green-dark) 0%,#4f9d3a 45%,var(--green-light) 100%)}

  /* front */
  .front__decoration{position:absolute;left:70px;top:20px;width:320px;height:190px;
    background:radial-gradient(ellipse at center,rgba(108,191,63,.10),rgba(108,191,63,0) 70%)}
  .person{position:absolute;left:44px;top:150px}
  .person__name{font-family:"Russo One",sans-serif;font-weight:400;font-size:25px;color:var(--green);letter-spacing:.5px;text-transform:uppercase}
  .person__title{font-family:"Arimo",sans-serif;font-size:17px;color:var(--ink);margin-top:2px}
  .contact{list-style:none;margin-top:16px;font-family:"Arimo",sans-serif;font-size:17px;color:var(--ink)}
  .contact li{display:flex;align-items:center;gap:8px;line-height:24px}
  .contact svg{width:14px;height:14px;flex:none}
  .company{position:absolute;right:40px;top:190px;display:flex;align-items:center;gap:10px;
    font-family:"Arimo",sans-serif;font-weight:700;font-size:20px;color:var(--ink);white-space:nowrap}
  .company__mark{width:14px;height:14px;background:var(--green);flex:none}
  .web{position:absolute;right:40px;bottom:34px;left:330px;border-top:1px solid var(--rule);padding-top:12px;
    font-family:"Arimo",sans-serif;font-size:17px;color:var(--ink);list-style:none}
  .web li{display:flex;justify-content:flex-end;align-items:center;gap:8px;line-height:24px}
  .web svg{width:15px;height:15px;flex:none}

  /* back */
  .back__decoration{position:absolute;left:120px;top:60px;width:380px;height:260px;
    background:radial-gradient(ellipse at center,rgba(255,255,255,.08),rgba(255,255,255,0) 70%)}
  .services{position:absolute;list-style:none;font-family:"Arimo",sans-serif;font-size:17px;color:#fff;text-transform:uppercase;letter-spacing:.5px}
  .services li{line-height:25px;padding-left:18px;position:relative;white-space:nowrap}
  .services li::before{content:"";position:absolute;left:0;top:9px;width:7px;height:7px;border-radius:50%;background:#fff}
  .services--main{left:48px;top:56px}
  .services--trades{left:370px;top:118px}
</style>
</head>
<body>
<main class="sheet">
  <section class="card card--front" aria-label="Business card front">
    <div class="front__decoration" role="img" aria-label="Faint green excavator and house decoration"></div>
    <div class="person">
      <h1 class="person__name">Tomasz Brelwik</h1>
      <p class="person__title">Managing Director</p>
      <ul class="contact">
        <li><svg viewBox="0 0 16 16"><path d="M4 1l3 3-2 2c1 2 3 4 5 5l2-2 3 3-2 3C7 15 1 9 1 3z" fill="var(--green)"/></svg>020 5194 6281</li>
        <li><svg viewBox="0 0 16 16"><rect x="4" y="1" width="8" height="14" rx="1.5" fill="none" stroke="var(--green)" stroke-width="1.8"/><circle cx="8" cy="12.5" r="1" fill="var(--green)"/></svg>07845139072</li>
      </ul>
    </div>
    <p class="company"><span class="company__mark"></span>Varkelt Construction Ltd</p>
    <ul class="web">
      <li>tomasz@varkelt.co.uk<svg viewBox="0 0 16 16"><rect x="1" y="3" width="14" height="10" fill="var(--green)"/><path d="M1 3l7 6 7-6" fill="none" stroke="#fff" stroke-width="1.3"/></svg></li>
      <li>www.varkelt.co.uk<svg viewBox="0 0 16 16"><circle cx="8" cy="8" r="6.5" fill="none" stroke="var(--green)" stroke-width="1.8"/><path d="M1.5 8h13M8 1.5c-3 3-3 10 0 13M8 1.5c3 3 3 10 0 13" fill="none" stroke="var(--green)" stroke-width="1.2"/></svg></li>
    </ul>
  </section>

  <section class="card card--back" aria-label="Business card back">
    <div class="back__decoration" role="img" aria-label="Faint excavator and house decoration"></div>
    <ul class="services services--main">
      <li>Kitchen Renovations</li>
      <li>Bathroom Renovations</li>
      <li>House Renovations</li>
      <li>Garage Conversions</li>
      <li>Extensions</li>
      <li>Loft Conversions</li>
      <li>Conservatories</li>
      <li>Carpentry</li>
    </ul>
    <ul class="services services--trades">
      <li>Tiling</li>
      <li>Electrical</li>
      <li>Plumbing &amp; Heating</li>
      <li>Bricklaying</li>
      <li>Landscaping</li>
      <li>Decorating</li>
      <li>Plastering</li>
    </ul>
  </section>
</main>
</body>
</html>
```